American cannabis tech company business card design

Pavrel.com is seeking a modern, professional, and brand-aligned business card that represents our company and its core values: Mission, Story, Values, and Impact. As an innovative cannabis company, we want a business card that is not only visually appealing but also serves as a representation of who we are and what we stand for.

Project Scope: Design a double-sided business card that integrates our brand identity and core values. Incorporate our key brand elements, ensuring a sleek and contemporary aesthetic. Visually reflect our core values (Mission, Story, Values, Impact) in a way that is engaging yet professional.

Target Market(s)

Vendors, third parties,

Contact Information for Business Card

Contact details (name, title, email, phone, website, etc.)

Font styles to use
Other font styles liked:
• Caslon, Centra

Colors

Designer to choose colors to be used in the design.

Requirements
Must have
• Pavrel.com logo and branding A creative yet clean way to integrate our core values (Mission, Story, Values, Impact) Modern typography and a well-structured layout
Nice to have
• forest green, grey, white, black
Should not have
• references to marijuana, leafs, plants, or related product

```html
<!DOCTYPE html>
<html lang="en">
<head>
<meta charset="utf-8">
<title>Pavrel.com Business Card</title>
<link rel="stylesheet" href="https://fonts.googleapis.com/css2?family=Poppins:wght@400;600&display=swap">
<style>
  :root {
    --forest: #16321a;
    --ink: #222222;
    --paper: #ffffff;
    --stage: #9a9a9a;
    --silver: #cfd1d0;
  }
  * { margin: 0; padding: 0; box-sizing: border-box; }
  html, body {
    width: 1093px;
    height: 1200px;
    overflow: hidden;
    background: var(--stage);
    font-family: "Poppins", sans-serif;
  }
  .canvas { position: relative; width: 1093px; height: 1200px; }

  .card {
    position: absolute;
    left: 264px;
    border-radius: 27px;
    overflow: hidden;
  }
  .card--front {
    top: 226px;
    width: 578px;
    height: 356px;
    background: var(--paper);
  }
  .card--back {
    top: 621px;
    width: 582px;
    height: 357px;
    background: var(--forest);
  }

  .front__band {
    position: absolute;
    left: 0; right: 0; bottom: 0;
    height: 12px;
    background: var(--forest);
  }
  .front__marker {
    position: absolute;
    left: 0; top: 42px;
    width: 19px; height: 35px;
    background: var(--forest);
  }
  .identity {
    position: absolute;
    left: 29px; top: 38px;
    line-height: 1;
  }
  .identity__name {
    font-weight: 600;
    font-size: 22.5px;
    color: var(--forest);
    letter-spacing: -0.2px;
  }
  .identity__title {
    margin-top: 1px;
    font-weight: 400;
    font-size: 17.5px;
    color: var(--ink);
  }
  .wordmark {
    position: absolute;
    font-weight: 600;
    letter-spacing: -1px;
    line-height: 1;
  }
  .wordmark--front {
    right: 34px; top: 40px;
    font-size: 52px;
    color: var(--forest);
  }
  .wordmark--back {
    left: 0; right: 0; top: 148px;
    text-align: center;
    font-size: 62px;
    color: var(--silver);
  }

  .contacts {
    position: absolute;
    left: 26px; top: 266px;
    list-style: none;
  }
  .contacts__item {
    display: flex;
    align-items: center;
    height: 26px;
    font-size: 17.5px;
    color: var(--ink);
  }
  .contacts__icon { width: 25px; height: 25px; margin-right: 5px; flex: none; }
  .website {
    position: absolute;
    right: 34px; top: 292px;
    font-size: 17.5px;
    color: var(--ink);
    line-height: 26px;
  }
</style>
</head>
<body>
<main class="canvas">
  <section class="card card--front" aria-label="Business card front">
    <div class="front__marker"></div>
    <div class="identity">
      <p class="identity__name">DANIEL REYES</p>
      <p class="identity__title">Managing Director</p>
    </div>
    <p class="wordmark wordmark--front">PAVREL</p>

    <ul class="contacts">
      <li class="contacts__item">
        <svg class="contacts__icon" viewBox="0 0 24 24" aria-hidden="true">
          <circle cx="12" cy="12" r="12" fill="#16321a"/>
          <path d="M8.2 6.5c.5-.4 1.1-.3 1.4.2l1 1.7c.3.5.2 1-.2 1.3l-.7.5c.5 1.3 1.6 2.5 2.9 3.1l.5-.7c.3-.4.9-.5 1.3-.2l1.7 1c.5.3.6.9.2 1.4l-.6.8c-.5.6-1.4.8-2.2.5-2.7-1-4.8-3.1-5.8-5.8-.3-.8-.1-1.7.5-2.2z" fill="#fff"/>
          <path d="M13.2 7.2a3.6 3.6 0 0 1 3.4 3.4M13.4 5a5.8 5.8 0 0 1 5.4 5.4" stroke="#fff" stroke-width="1" fill="none" stroke-linecap="round"/>
        </svg>
        <span>044-987 654 321</span>
      </li>
      <li class="contacts__item">
        <svg class="contacts__icon" viewBox="0 0 24 24" aria-hidden="true">
          <circle cx="12" cy="12" r="12" fill="#16321a"/>
          <rect x="5.5" y="8" width="13" height="8.5" rx="1" fill="none" stroke="#fff" stroke-width="1.2"/>
          <path d="M5.8 8.4 12 13l6.2-4.6M5.8 16.2l4.4-4M18.2 16.2l-4.4-4" fill="none" stroke="#fff" stroke-width="1.1"/>
        </svg>
        <span>info@pavrel.com</span>
      </li>
    </ul>
    <p class="website">www.pavrel.com</p>
    <div class="front__band"></div>
  </section>

  <section class="card card--back" aria-label="Business card back">
    <p class="wordmark wordmark--back">PAVREL</p>
  </section>
</main>
</body>
</html>
```